3D Printing Website redesign

We are in the process of redesigning our website. Attached is an image of one of the proposed pages - "The Quillmarrow". The idea with this page is that site visitors can get an indicative estimate of the cost of 3D Printing based on some provided metrics. When the user alters the metrics the price changes accordingly. We are looking for a design to support this page that will also be used across our site.

Reason: Allow more time for designers to submit designs

Reason: Still looking for the design to blow us away!

Printing

```html
<!DOCTYPE html>
<html lang="en">
<head>
<meta charset="utf-8">
<title>Quillmarrow Print Co.</title>
<link rel="stylesheet" href="https://fonts.googleapis.com/css2?family=Source+Sans+3:wght@400;600&family=PT+Sans+Narrow:wght@400;700&display=swap">
<style>
:root{
  --page:#f1f1f2;
  --ink:#3a3a3a;
  --muted:#6b6b6b;
  --blue:#254c88;
  --blue-dark:#1d3c6e;
  --hero:#28487f;
  --hero-text:#c9d3e6;
  --quote:#8596b8;
  --active:#0db2ec;
  --field:#e4e6f0;
  --tile:#d2d2d2;
  --caption:#2a2a2a;
  --button:#777777;
  --link:#274b8a;
  --white:#ffffff;
}
*{box-sizing:border-box;margin:0;padding:0}
html,body{width:1200px;height:895px;overflow:hidden}
body{position:relative;background:var(--page);font-family:"Source Sans 3",sans-serif;color:var(--ink)}
.abs{position:absolute}

.contact{left:126px;top:11px;font-size:15px;line-height:17.5px;color:var(--muted);font-style:normal}
.brand{left:508px;top:28px;display:flex;align-items:center;gap:14px}
.brand-dot{width:56px;height:56px;border-radius:50%;background:var(--blue)}
.brand-name{font-size:32px;font-weight:600;color:var(--blue)}
.account{left:1047px;top:0;width:50px;height:47px;background:var(--blue);display:flex;align-items:center;justify-content:center}
.search{left:872px;top:58px;width:225px;height:47px;background:var(--field);border:1px solid var(--blue);display:flex;align-items:center;justify-content:space-between;padding:0 16px 0 18px;font-size:15px;color:var(--ink)}

.hero{left:0;top:112px;width:1200px;height:360px;background:linear-gradient(#24427a,var(--hero) 40%,#244377);box-shadow:0 3px 6px rgba(0,0,0,.35)}
.hero-title{left:130px;top:174px;font-size:40px;line-height:44px;font-weight:400;color:var(--white);white-space:nowrap}
.hero-copy{left:130px;top:222px;width:510px;font-size:12px;line-height:20px;color:var(--hero-text)}
.hero-quote{left:739px;top:176px;width:360px;font-size:19px;line-height:24px;color:var(--quote)}
.hero-cite{right:102px;top:252px;font-size:19px;line-height:24px;color:var(--white)}
.hero-rule{left:230px;top:294px;width:810px;height:2px;background:radial-gradient(ellipse at center,#6f90c8,rgba(60,100,170,0) 70%)}
.feature{top:318px;width:240px}
.feature h3{font-weight:400;font-size:29px;line-height:34px;color:var(--white);margin-bottom:6px}
.feature p{font-size:12px;line-height:20px;color:var(--hero-text);width:160px}
.feature .icon{float:left;width:34px;height:34px;margin:0 4px 0 0}

.nav{left:0;top:112px;width:1200px;height:56px;background:linear-gradient(#2a5393,var(--blue-dark));box-shadow:0 2px 4px rgba(0,0,0,.3)}
.nav a{position:absolute;top:0;height:56px;line-height:56px;text-align:center;color:var(--white);font-size:16px;font-weight:600;text-decoration:none;border-left:1px solid #1a3563;border-right:1px solid #3361a5}
.nav a.active{background:var(--active);border-color:var(--active)}

.section-title{left:129px;font-family:"PT Sans Narrow",sans-serif;font-size:28px;font-weight:400;color:var(--ink)}
.button{left:968px;width:101px;height:26px;background:var(--button);color:var(--white);font-family:"PT Sans Narrow",sans-serif;font-size:17px;line-height:26px;text-align:center;text-decoration:none}
.card{top:546px;width:294px;height:173px;background:var(--white);border:1px solid #cfcfcf;padding:5px}
.card .shot{width:282px;height:161px;background:var(--tile);position:relative}
.card .caption{position:absolute;left:0;bottom:0;width:100%;height:32px;background:var(--caption);color:var(--white);font-family:"PT Sans Narrow",sans-serif;font-size:17px;line-height:32px;padding-left:16px}
.divider{left:130px;top:762px;width:939px;border-top:1px dashed #c4c4c4}

.post-thumb{left:129px;top:835px;width:294px;height:80px;background:var(--white);border:1px solid #cfcfcf;padding:5px}
.post-thumb div{width:100%;height:100%;background:var(--tile)}
.post-title{font-family:"PT Sans Narrow",sans-serif;font-weight:400;color:var(--ink)}
.post-meta{left:441px;top:867px;font-size:13px;color:#8a8a8a}
.post-meta a{color:var(--link);text-decoration:none}
.side-thumb{left:795px;top:835px;width:89px;height:80px;background:var(--white);border:1px solid #cfcfcf;padding:4px}
.side-thumb div{width:100%;height:100%;background:var(--tile)}
.side-text{left:897px;top:858px;width:160px;font-size:13px;line-height:20px;color:var(--ink)}
</style>
</head>
<body>

<header>
  <address class="abs contact">
    Quillmarrow Print Co.<br>
    Unit 12, 41 Harbour Lane, Millers Point, Sydney 2000<br>
    Ph: 61 2 5550 1482<br>
    M: 0400 555 273<br>
    e-mail: hello@quillmarrowprint.example
  </address>
  <div class="abs brand"><span class="brand-dot"></span><span class="brand-name">Quillmarrow</span></div>
  <div class="abs account" aria-label="Account">
    <svg width="24" height="24" viewBox="0 0 24 24" fill="#fff"><circle cx="12" cy="7" r="5.5"/><path d="M1 23c0-6 5-9.5 11-9.5S23 17 23 23z"/></svg>
  </div>
  <div class="abs search"><span>Search...</span>
    <svg width="19" height="19" viewBox="0 0 20 20" fill="none" stroke="#222" stroke-width="2.4"><circle cx="8" cy="8" r="6"/><path d="M12.5 12.5 18 18"/></svg>
  </div>
</header>

<section class="abs hero"></section>
<h1 class="abs hero-title">Welcome to our company</h1>
<p class="abs hero-copy">Sed gravida ligula vel arcu luctus sed tristique quam pharetra. Phasellus nisl libero, varius nec trist interdum ac, commodo et felis. Praesent porttitor facilisis dictum. Vivamus nulla mi, ultricies et dictu dignissim quis, egestas at nulla gravida ligula vel arcu luctus sed tristique quam.</p>
<blockquote class="abs hero-quote">“Sed gravida ligula vel arcu luctus sed tristique quam pharetra porttitor vel facilisis dictum vel arcu igula quam.”</blockquote>
<p class="abs hero-cite">Sed Gravida</p>
<div class="abs hero-rule"></div>

<div class="abs feature" style="left:130px">
  <h3>Sed gravida</h3>
  <svg class="icon" viewBox="0 0 34 34" fill="#fff"><circle cx="12" cy="12" r="7"/><g stroke="#fff" stroke-width="3.4"><path d="M12 2v20M2 12h20M5 5l14 14M19 5 5 19"/></g><circle cx="12" cy="12" r="2.5" fill="#28487f"/><circle cx="26" cy="26" r="5"/><g stroke="#fff" stroke-width="2.6"><path d="M26 19v14M19 26h14"/></g></svg>
  <p>Sed gravida ligula vel arcu luctus sed tristique quam pharetra. Phasellus nisl varius nec interdum ac.</p>
</div>
<div class="abs feature" style="left:378px">
  <h3>Arcus luctus</h3>
  <svg class="icon" viewBox="0 0 34 34" fill="#fff"><circle cx="12" cy="11" r="10"/><rect x="7" y="20" width="10" height="6"/><rect x="8" y="27" width="8" height="4" rx="2"/></svg>
  <p>Sed gravida ligula vel arcu luctus sed tristique quam pharetra. Phasellus nisl varius nec interdum ac.</p>
</div>
<div class="abs feature" style="left:626px">
  <h3>Varius nec</h3>
  <svg class="icon" viewBox="0 0 34 34"><circle cx="16" cy="16" r="15" fill="#fff"/><path d="M6 9c4 1 6 4 5 7s2 5 0 8c-2-1-5-4-6-8zM18 4c3 2 7 2 9 6-2 2-5 1-6 4 2 3 5 3 6 7-3 4-6 6-8 6 0-4 2-7 0-10-3-1-4-4-2-7 0-3 0-5 1-6z" fill="#28487f"/></svg>
  <p>Sed gravida ligula vel arcu luctus sed tristique quam pharetra. Phasellus nisl varius nec interdum ac.</p>
</div>
<div class="abs feature" style="left:874px">
  <h3>Commodo et felis</h3>
  <svg class="icon" viewBox="0 0 34 34"><text x="0" y="30" font-family="Source Sans 3, sans-serif" font-weight="600" font-size="36" fill="#fff">$</text></svg>
  <p>Sed gravida ligula vel arcu luctus sed tristique quam pharetra. Phasellus nisl varius nec interdum ac.</p>
</div>

<nav class="abs nav">
  <a href="#" style="left:102px;width:77px">HOME</a>
  <a href="#" style="left:178px;width:80px">SHOP</a>
  <a href="#" class="active" style="left:258px;width:87px">PRICES</a>
  <a href="#" style="left:345px;width:110px">MATERIALS</a>
  <a href="#" style="left:697px;width:102px">GALLERY</a>
  <a href="#" style="left:799px;width:107px">TRAINING</a>
  <a href="#" style="left:906px;width:112px">ABOUT US</a>
  <a href="#" style="left:1018px;width:79px">BLOG</a>
</nav>

<h2 class="abs section-title" style="top:500px">Latest from our Portfolio</h2>
<a class="abs button" style="top:505px" href="#">View Portfolio</a>

<div class="abs card" style="left:129px"><div class="shot" role="img" aria-label="Project 1 photo"><div class="caption">Lorem ipsum Project 1</div></div></div>
<div class="abs card" style="left:452px"><div class="shot" role="img" aria-label="Project 2 photo"><div class="caption">Lorem ipsum Project 2</div></div></div>
<div class="abs card" style="left:775px"><div class="shot" role="img" aria-label="Project 3 photo"><div class="caption">Lorem ipsum Project 3</div></div></div>

<div class="abs divider"></div>

<h2 class="abs section-title" style="top:787px">Latest from our Blog</h2>
<a class="abs button" style="top:795px" href="#">View Blog</a>

<div class="abs post-thumb"><div role="img" aria-label="Blog post photo"></div></div>
<h3 class="abs post-title" style="left:441px;top:830px;font-size:28px">Commodo et felis</h3>
<p class="abs post-meta">Posted on September 12, 2011 by <a href="#">Admin</a> in <a href="#">Random</a><br>Tags: <a href="#">Type</a>, <a href="#">Glossy</a>, <a href="#">Curl</a></p>

<div class="abs side-thumb"><div role="img" aria-label="Blog post thumbnail"></div></div>
<h3 class="abs post-title" style="left:898px;top:832px;font-size:22px">Commodo et felis</h3>
<p class="abs side-text">Sed gravida ligula vel arcu lutus sed etistristique...</p>

</body>
</html>
```